Business card design Needed for new logo / Construction business, home extensions and new builds

We need a business card design using our new logo files which i will attach to this project :)

We are a small construction business specialising in home extensions, new builds and property development. We are very ambitious and would appreciate professional and elegant designs for our new business card.

Very serious about using the services on MakerQuarry and recently acquired our new logo from here :)

Please get involved, i will feedback when i can as i am very busy but can respond daily, thanks

Target Market(s)

People that want to build onto their houses, new building developments or adding too their existing property

Industry/Entity Type

Construction

Contact Information for Business Card

Renwick Tolliver Construction, Lionel Ashby (Managing Director), Tel 07822254961, email - info@renwick-tolliver, www.renwick-tolliver.co.uk

Colors

Designer to choose colors to be used in the design.

Requirements
Must have
• I like a deep grey on the back please. A lot of you have provided black from and back, try mixing things up a little. The black looks cool 😎 Thanks

```html
<!DOCTYPE html>
<html lang="en">
<head>
<meta charset="utf-8">
<title>Renwick Tolliver Construction – Business Card</title>
<link href="https://fonts.googleapis.com/css2?family=Cinzel:wght@500&family=Montserrat:wght@400;700&display=swap" rel="stylesheet">
<style>
  :root {
    --backdrop: #454545;
    --card-black: #101010;
    --gold: #e2b44a;
    --gold-light: #f3d27e;
    --gold-dark: #b8862a;
    --white: #ffffff;
    --silver-light: #c9cbcd;
    --silver-mid: #9ea3a8;
    --silver-dark: #8a9097;
    --emboss: #161616;
  }
  * { margin: 0; padding: 0; box-sizing: border-box; }
  html, body {
    width: 1200px; height: 801px; overflow: hidden;
    background: var(--backdrop);
  }
  .canvas {
    position: relative; width: 1200px; height: 801px;
    display: flex; align-items: center; justify-content: center; gap: 40px;
  }
  .card {
    position: relative; width: 530px; height: 303px;
    border-radius: 16px; border: 2px solid var(--gold);
    overflow: hidden;
  }

  /* Front */
  .card--front { background: var(--card-black); }
  .front__tab {
    position: absolute; top: 0; right: 40px; width: 46px; height: 16px;
    background: linear-gradient(90deg, var(--gold-dark), var(--gold-light), var(--gold));
  }
  .front__person {
    position: absolute; top: 34px; right: 40px; text-align: right;
    font-family: "Montserrat", sans-serif;
  }
  .person__name {
    color: var(--gold); font-weight: 700; font-size: 21px; letter-spacing: 0.5px;
  }
  .person__role {
    color: var(--white); font-weight: 400; font-size: 13px; letter-spacing: 0.8px; margin-top: 2px;
  }
  .front__deco {
    position: absolute; right: 62px; top: 112px; width: 130px; height: 130px;
    background: var(--emboss); border-radius: 6px;
    box-shadow: inset 1px 1px 0 #242424, inset -1px -1px 0 #050505;
  }
  .front__brand {
    position: absolute; left: 36px; top: 82px;
    display: flex; align-items: center; gap: 10px;
  }
  .brand__mark { width: 12px; height: 12px; background: var(--gold); }
  .brand__name {
    font-family: "Cinzel", serif; font-weight: 500; color: var(--gold);
    font-size: 17px; line-height: 1.25; letter-spacing: 1px;
  }
  .front__details {
    position: absolute; left: 58px; top: 160px;
    font-family: "Montserrat", sans-serif; color: var(--white);
    font-size: 12.5px; letter-spacing: 0.4px; line-height: 1.35;
  }
  .details__address { margin-bottom: 10px; }
  .contact-list { list-style: none; }
  .contact-list li { display: flex; align-items: center; gap: 7px; }
  .contact-list svg { width: 11px; height: 11px; flex: none; }

  /* Back */
  .card--back {
    background: linear-gradient(120deg, var(--silver-light) 0%, var(--silver-dark) 35%, var(--silver-mid) 60%, var(--silver-light) 100%);
    display: flex; flex-direction: column; align-items: center; justify-content: center; gap: 14px;
  }
  .back__mark { width: 22px; height: 22px; background: var(--white); }
  .back__name {
    font-family: "Cinzel", serif; font-weight: 500; color: var(--white);
    text-align: center; letter-spacing: 2px;
  }
  .back__name .line-main { display: block; font-size: 34px; }
  .back__name .line-sub { display: block; font-size: 34px; }
</style>
</head>
<body>
<main class="canvas">
  <section class="card card--front" aria-label="Card front">
    <div class="front__tab"></div>
    <div class="front__person">
      <p class="person__name">LIONEL ASHBY</p>
      <p class="person__role">Managing Director</p>
    </div>
    <div class="front__deco" aria-hidden="true"></div>
    <div class="front__brand">
      <span class="brand__mark"></span>
      <p class="brand__name">RENWICK TOLLIVER<br>CONSTRUCTION</p>
    </div>
    <div class="front__details">
      <p class="details__address">Your address, City<br>State, Zip 1234</p>
      <ul class="contact-list">
        <li>
          <svg viewBox="0 0 12 12"><path fill="var(--gold)" d="M2.5 1h2l1 3-1.3 1a6.5 6.5 0 0 0 2.8 2.8L8 6.5l3 1v2A1.5 1.5 0 0 1 9.5 11 8.5 8.5 0 0 1 1 2.5 1.5 1.5 0 0 1 2.5 1z"/></svg>
          07822254961
        </li>
        <li>
          <svg viewBox="0 0 12 12"><rect x="0.5" y="2" width="11" height="8" rx="1" fill="var(--gold)"/><path d="M1 2.6 6 6.6l5-4" fill="none" stroke="var(--card-black)" stroke-width="1"/></svg>
          info@renwick-tolliver
        </li>
        <li>
          <svg viewBox="0 0 12 12"><circle cx="6" cy="6" r="5.3" fill="var(--gold)"/><path d="M0.7 6h10.6M6 0.7c-2.6 2.8-2.6 7.8 0 10.6M6 0.7c2.6 2.8 2.6 7.8 0 10.6" fill="none" stroke="var(--card-black)" stroke-width="0.8"/></svg>
          www.renwick-tolliver.co.uk
        </li>
      </ul>
    </div>
  </section>

  <section class="card card--back" aria-label="Card back">
    <span class="back__mark"></span>
    <p class="back__name">
      <span class="line-main">RENWICK TOLLIVER</span>
      <span class="line-sub">CONSTRUCTION</span>
    </p>
  </section>
</main>
</body>
</html>
```